Business card for medical clinic

I need an upmarket, modern medical/health business card for my clinic

Contact Information for Business Card

name, address, email, qr code

```html
<!DOCTYPE html>
<html lang="en">
<head>
<meta charset="utf-8">
<title>Novara Health – Business Card</title>
<link href="https://fonts.googleapis.com/css2?family=Montserrat:wght@400;700&display=swap" rel="stylesheet">
<style>
  :root {
    --page-bg: #e8e5e1;
    --frost-light: #e3dace;
    --frost-mid: #d3c6b6;
    --panel-dark: #161616;
    --panel-mid: #2f2e2d;
    --accent-teal: #2a86a3;
    --accent-teal-deep: #1f5f7a;
    --text-light: #d3cabf;
    --icon-grey: #8b857e;
  }
  * { margin: 0; padding: 0; box-sizing: border-box; }
  html, body {
    width: 1200px;
    height: 1047px;
    overflow: hidden;
    background: var(--page-bg);
    font-family: "Montserrat", sans-serif;
  }
  .card {
    position: absolute;
    left: 120px;
    top: 261px;
    width: 960px;
    height: 524px;
    border-radius: 20px;
    overflow: hidden;
    box-shadow: 0 18px 40px rgba(0,0,0,0.18);
  }
  .card-surface {
    position: absolute;
    inset: 0;
    width: 960px;
    height: 524px;
  }
  .brand {
    position: absolute;
    left: 40px;
    top: 44px;
    display: flex;
    align-items: center;
    gap: 18px;
  }
  .brand-dot {
    width: 74px;
    height: 74px;
    border-radius: 50%;
    border: 5px solid var(--accent-teal);
  }
  .brand-name {
    font-weight: 400;
    font-size: 27px;
    letter-spacing: 2px;
    color: var(--accent-teal);
  }
  .name-marker {
    position: absolute;
    left: 8px;
    top: 185px;
    width: 21px;
    height: 64px;
    background: var(--accent-teal);
  }
  .person-name {
    position: absolute;
    left: 41px;
    top: 188px;
    font-weight: 700;
    font-size: 35px;
    letter-spacing: 0.5px;
    color: var(--accent-teal);
  }
  .person-role {
    position: absolute;
    left: 41px;
    top: 224px;
    font-size: 24px;
    color: var(--text-light);
  }
  .address {
    position: absolute;
    left: 41px;
    top: 290px;
    font-size: 24px;
    line-height: 38px;
    color: var(--text-light);
  }
  .contact-list {
    position: absolute;
    left: 41px;
    top: 386px;
    list-style: none;
  }
  .contact-item {
    display: flex;
    align-items: center;
    gap: 12px;
    height: 36.5px;
    font-size: 24px;
    color: var(--text-light);
  }
  .contact-icon {
    width: 20px;
    height: 20px;
    fill: var(--icon-grey);
  }
</style>
</head>
<body>
  <article class="card">
    <svg class="card-surface" viewBox="0 0 960 524" aria-hidden="true">
      <defs>
        <linearGradient id="frost" x1="0" y1="0" x2="1" y2="1">
          <stop offset="0" stop-color="var(--frost-light)"/>
          <stop offset="1" stop-color="var(--frost-mid)"/>
        </linearGradient>
        <linearGradient id="panel" x1="0" y1="0" x2="1" y2="0.4">
          <stop offset="0" stop-color="var(--panel-mid)"/>
          <stop offset="0.6" stop-color="var(--panel-dark)"/>
          <stop offset="1" stop-color="#232221"/>
        </linearGradient>
      </defs>
      <rect class="frost-area" width="960" height="524" fill="url(#frost)"/>
      <path class="dark-panel" d="M0 0 H596 A278 278 0 0 0 596 524 H0 Z" fill="url(#panel)"/>
    </svg>

    <div class="brand">
      <span class="brand-dot"></span>
      <span class="brand-name">NOVARA HEALTH</span>
    </div>

    <span class="name-marker"></span>
    <h1 class="person-name">DANIEL MOORE</h1>
    <p class="person-role">Managing Director</p>

    <p class="address">Your address, City<br>State, Zip 1234</p>

    <ul class="contact-list">
      <li class="contact-item">
        <svg class="contact-icon" viewBox="0 0 24 24"><path d="M3 9c0-3 4-5 9-5s9 2 9 5l-4 1-1-3H8L7 10 3 9zm3 3h12l2 7H4l2-7zm6 1.5a2.5 2.5 0 1 0 0 5 2.5 2.5 0 0 0 0-5z"/></svg>
        123 456 789
      </li>
      <li class="contact-item">
        <svg class="contact-icon" viewBox="0 0 24 24"><path d="M2 6h20v13H2V6zm2 2v.4l8 5 8-5V8l-8 5-8-5z"/></svg>
        info@yourmail.com
      </li>
      <li class="contact-item">
        <svg class="contact-icon" viewBox="0 0 24 24"><path d="M12 2a10 10 0 1 0 0 20 10 10 0 0 0 0-20zm-1 3c-1 2-3 2-3 4s2 2 2 4-2 2-1 5c-3-1-5-4-5-6 0-4 3-7 7-7zm3 1c2 1 4 3 4 6 0 2-1 4-3 5 0-2 1-3 0-5s-3-1-3-3 2-2 2-3z"/></svg>
        www.yourwebsite.com
      </li>
    </ul>
  </article>
</body>
</html>
```